Torvane Email Signature Banners – Fabrication Capability Series

www.Torvane.com.au is an Australian engineering and fabrication company specialising in fabrication and welding of :
steel piping spools,
skids and frames,
small volume process steel tanks
and general steel fabrication
We require four distinct banner designs for use in Microsoft Lintaro email signatures. Each banner will highlight a specific capability while maintaining a consistent brand identity.
Deliverables
Four banners total:
Piping Spools Fabrication – focus on precision welding and stainless steel pipework
Skid & Frames Fabrication – highlight skid systems and structural frames
Small Steel Tanks Fabrication – show fabricated tanks and workshop craftsmanship
General Fabrication Solutions – broad steel fabrication theme for company-wide use
Dimensions: 600–700 px wide × 100 px high
Format: PNG (preferred), small file size prefered
Resolution: 72 dpi
Background: non-transparent, industrial or workshop setting
Text examples:
1. Piping Spools Fabrication
Option A: “Expert Fabrication Solutions for Process Piping”
Option B: “Precision Welding for Complex Systems”
Option C: “Delivering Quality in Every Spool”
Option D: “Engineered for Flow, Built for Strength”
2. Skid & Frames Fabrication
Option A: “Custom Engineered Modular Systems”
Option B: “Built Strong. Designed Smart.”
Option C: “Reliable Frames for Industrial Performance”
Option D: “Modular Fabrication for Seamless Integration”
3. Small Steel Tanks Fabrication
Option A: “Precision Built for Your Needs”
Option B: “Compact Strength. Proven Durability.”
Option C: “Fabricated for Performance and Longevity”
Option D: “Small Tanks. Big Reliability.”
4. General Fabrication Solutions
Option A: “Quality Craftsmanship, Proven Results”
Option B: “Your Partner in Precision Fabrication”
Option C: “Engineering Excellence in Every Weld”
Option D: “Australian Fabrication. Global Standards.”
Style Direction
Clean, professional, and engineering‑focused
Use Torvane brand colours
Blend photo realism with vector clarity (no heavy gradients)
Include subtle industrial textures or workshop imagery
Typography: bold sans‑serif, legible at small scale
Usage Context
These banners will appear at the bottom of staff email signatures via Lintaro Email Signature Tool for Microsoft 365, so clarity and fast loading are essential. No Logo is required in the banners.
Reference
Existing Torvane signature is attached. Colour palette to match the signature style and logo.
Target Market(s)
Engineering and construction companies,
Industry/Entity Type
Engineering fabrication design
Look and feel

```html
<!DOCTYPE html>
<html lang="en">
<head>
<meta charset="UTF-8">
<title>Torvane Email Signature Banners – Fabrication Capability Series</title>
<link rel="stylesheet" href="https://fonts.googleapis.com/css2?family=Lato:wght@300;400;700;900&display=swap">
<style>
  :root {
    --page: #ffffff;
    --navy: #1c335c;
    --navy-deep: #14274a;
    --navy-soft: #2a4675;
    --accent: #2aa4e2;
    --white: #ffffff;
  }
  * { margin: 0; padding: 0; box-sizing: border-box; }
  html, body { width: 1200px; height: 983px; overflow: hidden; background: var(--page); }
  body { position: relative; font-family: "Lato", Arial, sans-serif; color: var(--white); }

  .banner {
    position: absolute;
    width: 1081px;
    height: 154px;
    overflow: hidden;
    background: linear-gradient(90deg, var(--navy) 0%, var(--navy) 55%, var(--navy-soft) 100%);
    box-shadow: 0 6px 22px rgba(20, 39, 74, 0.18);
  }
  .banner::after {
    content: "";
    position: absolute; inset: 0;
    background: repeating-linear-gradient(90deg, rgba(255,255,255,0.025) 0 2px, transparent 2px 38px);
    pointer-events: none;
  }
  .banner--spools  { left: 60px; top: 79px; }
  .banner--skids   { left: 56px; top: 286px; }
  .banner--tanks   { left: 56px; top: 517px; }
  .banner--general { left: 56px; top: 747px; }

  .banner__art { position: absolute; left: 0; top: 0; width: 1081px; height: 154px; z-index: 1; }

  .banner__copy { position: absolute; z-index: 2; top: 0; }
  .banner--spools  .banner__copy { left: 502px; }
  .banner--skids   .banner__copy { left: 446px; }
  .banner--tanks   .banner__copy { left: 446px; }
  .banner--general .banner__copy { left: 492px; }

  .banner__title {
    position: absolute; white-space: nowrap;
    line-height: 42px; font-weight: 400; letter-spacing: 0.2px;
    text-transform: uppercase;
  }
  .banner__title strong { font-weight: 900; }
  .banner--spools  .banner__title { top: 26px; font-size: 37px; }
  .banner--skids   .banner__title { top: 26px; font-size: 38px; }
  .banner--tanks   .banner__title { top: 27px; font-size: 34px; }
  .banner--general .banner__title { top: 28px; font-size: 31px; }

  .banner__rule { position: absolute; top: 78px; width: 191px; height: 4px; background: var(--accent); }

  .banner__node { position: absolute; top: 75px; width: 70px; height: 12px; }
  .banner__node::before {
    content: ""; position: absolute; left: 0; right: 0; top: 5px; height: 2px; background: var(--accent);
  }
  .banner__node::after {
    content: ""; position: absolute; left: 29px; top: 0; width: 12px; height: 12px;
    border: 2px solid var(--accent); border-radius: 50%; background: var(--navy);
  }

  .banner__tagline { position: absolute; white-space: nowrap; font-weight: 400; }
  .banner--spools  .banner__tagline { top: 97px;  font-size: 28px; }
  .banner--skids   .banner__tagline { top: 100px; font-size: 24px; }
  .banner--tanks   .banner__tagline { top: 97px;  font-size: 28px; }
  .banner--general .banner__tagline { top: 97px;  font-size: 25px; }
</style>
</head>
<body>

  <section class="banner banner--spools">
    <svg class="banner__art" viewBox="0 0 1081 154">
      <defs>
        <linearGradient id="photo-welding" x1="0" y1="0" x2="1" y2="0.4">
          <stop offset="0" stop-color="#2b3644"/>
          <stop offset="0.45" stop-color="#355a86"/>
          <stop offset="0.7" stop-color="#4d8fcf"/>
          <stop offset="1" stop-color="#2c3a4c"/>
        </linearGradient>
      </defs>
      <polygon role="img" aria-label="Welder in protective mask welding a steel pipe spool with bright blue arc light"
               points="0,0 434,0 403,77 434,154 0,154" fill="url(#photo-welding)"/>
      <polygon points="434,0 457,0 426,77 457,154 434,154 403,77" fill="var(--accent)"/>
    </svg>
    <div class="banner__copy">
      <h2 class="banner__title">Piping Spools <strong>Fabrication</strong></h2>
      <span class="banner__rule"></span>
      <p class="banner__tagline">Precision Welding for Complex Systems</p>
    </div>
  </section>

  <section class="banner banner--skids">
    <svg class="banner__art" viewBox="0 0 1081 154">
      <defs>
        <linearGradient id="photo-cutting" x1="0" y1="0" x2="1" y2="1">
          <stop offset="0" stop-color="#1d4f8c"/>
          <stop offset="0.5" stop-color="#3d84cc"/>
          <stop offset="1" stop-color="#1b3258"/>
        </linearGradient>
        <linearGradient id="photo-machining" x1="0" y1="0" x2="1" y2="1">
          <stop offset="0" stop-color="#8a96a3"/>
          <stop offset="1" stop-color="#3e4a58"/>
        </linearGradient>
      </defs>
      <polygon role="img" aria-label="CNC machine cutting a steel plate with blue light"
               points="0,0 292,0 336,77 292,154 0,154" fill="url(#photo-cutting)"/>
      <polygon role="img" aria-label="Workshop machinery detail"
               points="310,0 390,0 430,0 400,58 348,58 318,8" fill="url(#photo-machining)"/>
      <polygon role="img" aria-label="Machined steel shaft close-up"
               points="348,72 400,72 432,126 400,154 348,154 316,126 340,84" fill="url(#photo-machining)"/>
      <polyline points="292,0 336,77 292,154" fill="none" stroke="var(--accent)" stroke-width="4"/>
      <polyline points="318,8 348,58 400,58 430,0" fill="none" stroke="var(--accent)" stroke-width="3"/>
      <polyline points="340,84 348,72 400,72 432,126 400,154" fill="none" stroke="var(--accent)" stroke-width="3"/>
    </svg>
    <div class="banner__copy">
      <h2 class="banner__title">Skid &amp; Frames <strong>Fabrication</strong></h2>
      <span class="banner__node"></span>
      <p class="banner__tagline">Reliable Frames for Industrial Performance</p>
    </div>
  </section>

  <section class="banner banner--tanks">
    <svg class="banner__art" viewBox="0 0 1081 154">
      <defs>
        <linearGradient id="photo-tanks" x1="0" y1="0" x2="1" y2="0">
          <stop offset="0" stop-color="#5c6b58"/>
          <stop offset="0.4" stop-color="#3a3f44"/>
          <stop offset="0.8" stop-color="#5b636b"/>
          <stop offset="1" stop-color="#3c4550"/>
        </linearGradient>
      </defs>
      <path role="img" aria-label="Fabricated steel tank sections with flanged nozzles in the workshop"
            d="M0 0 H350 Q396 77 350 154 H0 Z" fill="url(#photo-tanks)"/>
      <path d="M350 0 Q396 77 350 154 H364 Q412 77 364 0 Z" fill="var(--accent)"/>
    </svg>
    <div class="banner__copy">
      <h2 class="banner__title"><strong>Small Steel Tanks</strong> Fabrication</h2>
      <span class="banner__node"></span>
      <p class="banner__tagline">Fabricated for Performance and Longevity</p>
    </div>
  </section>

  <section class="banner banner--general">
    <svg class="banner__art" viewBox="0 0 1081 154">
      <defs>
        <linearGradient id="photo-workshop" x1="0" y1="0" x2="0" y2="1">
          <stop offset="0" stop-color="#2d4670"/>
          <stop offset="0.45" stop-color="#8d6a4c"/>
          <stop offset="0.6" stop-color="#c9792e"/>
          <stop offset="1" stop-color="#2e2f34"/>
        </linearGradient>
      </defs>
      <polygon role="img" aria-label="Steel fabrication workshop with rails and glowing sparks"
               points="0,0 398,0 422,154 0,154" fill="url(#photo-workshop)"/>
      <polygon points="398,0 416,0 440,154 422,154" fill="var(--accent)"/>
    </svg>
    <div class="banner__copy">
      <h2 class="banner__title">General <strong>Fabrication Solutions</strong></h2>
      <span class="banner__node"></span>
      <p class="banner__tagline">Australian Fabrication. Global Standards.</p>
    </div>
  </section>

</body>
</html>
```